Banner for construction site to identify developer

we need a 4 foot by 8 foot banner to hang on the fence of a residential townhome development in Phoenix, Arizona that identifies Tolvane Holdings as the company behind the development/project. Also needs to include the logo, phone number, and web address. Would like to stick with the blue colors provided in the attached logo. The blues should stay the same but the letters in the logo can change to another color if necessary. Feel free to use "Tolvane Holdings" in place of "Tolvane Holdings Group". Looking for use of colors/design to take up space so banner is not just text with a logo.

Target Market(s)

drive by traffic looking at the site

Industry/Entity Type

Real Estate

Colors
0054AA
0677BA
7BADD7
CADEEF
E8F1F8

Requirements
Must have
• company name, phone number and web address

```html
<!DOCTYPE html>
<html lang="en">
<head>
<meta charset="utf-8">
<title>Tolvane Holdings – Site Banner</title>
<link href="https://fonts.googleapis.com/css2?family=Open+Sans:wght@400;700;800&display=swap" rel="stylesheet">
<style>
  :root {
    --stage: #a9a9a9;
    --paper: #ffffff;
    --brand-blue: #1fa6d9;
    --band-blue: #1f6fa0;
    --charcoal: #3f3f42;
    --ink: #3b3b3e;
    --white: #ffffff;
  }
  * { box-sizing: border-box; margin: 0; padding: 0; }
  html, body {
    width: 921px;
    height: 1200px;
    overflow: hidden;
  }
  body {
    background: var(--stage);
    font-family: "Open Sans", Arial, sans-serif;
    position: relative;
  }
  .banner {
    position: absolute;
    left: 40px;
    top: 390px;
    width: 841px;
    height: 420px;
    box-shadow: 0 10px 24px rgba(0,0,0,0.35);
    display: flex;
    flex-direction: column;
  }
  .banner__brand {
    height: 200px;
    background: var(--paper);
    display: flex;
    align-items: flex-end;
    justify-content: center;
    gap: 18px;
    padding-bottom: 26px;
  }
  .brand-mark {
    width: 58px;
    height: 58px;
    background: var(--brand-blue);
    margin-bottom: 10px;
  }
  .brand-name {
    font-weight: 800;
    font-size: 66px;
    line-height: 1;
    letter-spacing: -1.5px;
    color: var(--ink);
  }
  .banner__tagline {
    height: 70px;
    background: var(--band-blue);
    color: var(--white);
    display: flex;
    align-items: center;
    justify-content: center;
    font-weight: 800;
    font-size: 23px;
    letter-spacing: 0.2px;
    text-transform: uppercase;
  }
  .banner__contact {
    flex: 1;
    background: var(--charcoal);
    color: var(--white);
    display: flex;
    flex-direction: column;
    align-items: center;
    justify-content: center;
    gap: 2px;
  }
  .contact-phone {
    display: flex;
    align-items: center;
    gap: 12px;
    font-weight: 700;
    font-size: 52px;
    line-height: 1.1;
  }
  .phone-icon { width: 44px; height: 44px; }
  .contact-web {
    font-size: 42px;
    line-height: 1.15;
    font-weight: 400;
    letter-spacing: 1px;
  }
  .contact-web strong { font-weight: 700; letter-spacing: 0.5px; }
</style>
</head>
<body>
  <section class="banner">
    <header class="banner__brand">
      <span class="brand-mark" aria-hidden="true"></span>
      <h1 class="brand-name">Tolvane Holdings</h1>
    </header>
    <p class="banner__tagline">Crafting Phoenix's Premium Residential Townhomes</p>
    <div class="banner__contact">
      <p class="contact-phone">
        <svg class="phone-icon" viewBox="0 0 44 44" aria-hidden="true">
          <circle cx="22" cy="22" r="22" fill="var(--brand-blue)"/>
          <path d="M15.5 11.5c1-.6 2.1-.3 2.7.6l2.3 3.6c.6.9.4 2-.4 2.7l-1.6 1.3c1 2.3 2.9 4.4 5.2 5.6l1.4-1.5c.7-.8 1.9-.9 2.7-.3l3.5 2.5c.9.6 1.1 1.8.5 2.7l-1.3 1.9c-.9 1.3-2.6 1.9-4.1 1.4-6.2-2-11.1-7.2-12.8-13.5-.4-1.5.2-3 1.5-3.8z" fill="var(--charcoal)"/>
          <path d="M24 12.5a8 8 0 0 1 7.5 7.5M24 16.5a4 4 0 0 1 3.5 3.5" stroke="var(--charcoal)" stroke-width="2" fill="none" stroke-linecap="round"/>
        </svg>
        (480) 555-0147
      </p>
      <p class="contact-web">www.<strong>tolvaneholdings</strong>.com</p>
    </div>
  </section>
</body>
</html>
```